Corporate Design für Hausverwalterin und Immobilienvermarktung
Zielgruppe
Hausverwalterin und Immobilienvermarktung
Aufgabenstellung
wir sind im Immobiliensektor unterwegs und das Design soll edel und hochwertig sein

```html
<!DOCTYPE html>
<html lang="de">
<head>
<meta charset="utf-8">
<title>Varenta Immobilien – Visitenkarte</title>
<link rel="stylesheet" href="https://fonts.googleapis.com/css2?family=Cinzel:wght@400;500;600&display=swap">
<style>
  :root {
    --navy: #12263d;
    --gold: #c9a22e;
    --ivory: #f1ede4;
    --page: #ffffff;
    --shadow: rgba(0, 0, 0, 0.38);
  }
  * { margin: 0; padding: 0; box-sizing: border-box; }
  html, body {
    width: 1200px;
    height: 2537px;
    overflow: hidden;
    background: var(--page);
  }
  .sheet {
    position: relative;
    width: 1200px;
    height: 2537px;
    font-family: "Cinzel", "Times New Roman", serif;
  }
  .card {
    position: absolute;
    left: 183px;
    width: 850px;
    height: 563px;
    background: var(--navy);
    box-shadow: 22px 30px 40px var(--shadow);
  }
  .card--front { top: 633px; }
  .card--back  { top: 1343px; }

  /* Front */
  .brand {
    position: absolute;
    left: 0; right: 0;
    top: 150px;
    text-align: center;
    color: var(--gold);
  }
  .brand__mark {
    display: block;
    width: 34px;
    height: 34px;
    margin: 0 auto 62px;
    background: var(--gold);
  }
  .brand__name {
    font-size: 56px;
    font-weight: 500;
    letter-spacing: 3px;
    line-height: 1.1;
  }
  .brand__tagline {
    margin-top: 12px;
    font-size: 27px;
    font-weight: 400;
    letter-spacing: 1.5px;
  }

  /* Back */
  .info {
    position: absolute;
    left: 0; right: 0;
    top: 72px;
    text-align: center;
    color: var(--ivory);
    font-size: 20.5px;
    line-height: 28px;
    letter-spacing: 0.6px;
  }
  .info__headline { margin-bottom: 28px; }
  .info__intro { margin-bottom: 36px; }
  .services {
    list-style: none;
    display: inline-block;
    text-align: left;
    color: var(--gold);
    font-weight: 600;
    margin-bottom: 44px;
  }
  .services li::before {
    content: "•";
    margin-right: 10px;
  }
  .contact p { margin: 0; }
</style>
</head>
<body>
<main class="sheet">

  <section class="card card--front" aria-label="Vorderseite">
    <div class="brand">
      <span class="brand__mark"></span>
      <h1 class="brand__name">Varenta Immobilien</h1>
      <p class="brand__tagline">VERWALTUNG &amp; VERMARKTUNG</p>
    </div>
  </section>

  <section class="card card--back" aria-label="Rückseite">
    <div class="info">
      <p class="info__headline">GANZHEITLICHE IMMOBILIENBETREUUNG MIT STRATEGIE</p>
      <p class="info__intro">
        ALS ZERTIFIZIERTE HAUSVERWALTERIN &amp; IMMOBILIENMAKLERIN<br>
        GEMÄSS § 34C GEWO VERBINDE ICH KLASSISCHE<br>
        VERWALTUNG MIT WERTOPTIMIERTER VERMARKTUNG:
      </p>
      <ul class="services">
        <li>HAUSVERWALTUNG: RECHTSSICHER &amp; ENTLASTEND.</li>
        <li>ASSET MANAGEMENT: STRATEGISCHE ERTRAGSSTEIGERUNG.</li>
        <li>VERKAUF: MARKTGERECHT &amp; PROFESSIONELL.</li>
      </ul>
      <div class="contact">
        <p>VARENTA IMMOBILIEN - IHR EIGENTUM IN ZUVERLÄSSIGEN HÄNDEN.</p>
        <p>TELEFON: 0170 381 92 46</p>
        <p>E-MAIL: INFO@VARENTA-IMMOBILIEN.DE</p>
        <p>WEBSEITE: WWW.VARENTA-IMMOBILIEN.DE</p>
      </div>
    </div>
  </section>

</main>
</body>
</html>
```